Digital Marketing Website Redesign, modern, fresh, dynamic

Hi there, we would like to freshen up our website and create a new dynamic look. We are a digital marketing agency who specialise in digital transformation in the form of creating websites for appointment bookings. Our clients are service businesses such as hairdressers, dentists and doctors who's patients need to book appointments with them.

Our company name is Tallomex with the point being we can help increase your revenue curve by increasing your appointment bookings.

Our services include building the website, creating campaigns to drive traffic, increasing conversions and monitoring and reporting.

We are playing with a tagline of 'Step into your Digital Transformation' as we have a 5 step journey that customers can take with us getting them from zero to full appointment bookings.

Our current website is www.tallomex-sample.com

You can see a draft design that I mocked up on Canva here https://www.draftboard-sample.com/design/QXB82LmpR7T/KpoW39dnFsYbZet_wqe_OPa/edit?utm_content=QXB82LmpR7T&utm_campaign=designshare&utm_medium=link2&utm_source=sharebutton

Also attached some other homepage ideas. In regard to photos we are open to ideas.

Please let if you need any more information to provide us with an initial design. Thanks million and I look forward to receiving fantastic designs :)

Marian Dobbs
Tallomex

Target Market(s)

Appointment based businesses such as hairdressers, dentists, doctors

Industry/Entity Type

Marketing and Digital

Coding

Coded - Design and coding required

Number of Pages Required

1 page

Colors
0094D4
00A9DD
6FCCEA
C7EBF8
E9F6FB

Requirements
Must have
• Appointment booking CTA
Nice to have
• A website we like https://www.fergalwhitty-sample.ie

```html
<!DOCTYPE html>
<html lang="en">
<head>
<meta charset="utf-8">
<title>Tallomex – Step into your Digital Transformation</title>
<link href="https://fonts.googleapis.com/css2?family=Kumbh+Sans:wght@600;700;800&family=Roboto:wght@400;500;700&display=swap" rel="stylesheet">
<style>
:root{
  --blue:#1596d4;
  --blue-dark:#0b7fc0;
  --green:#b3c10c;
  --green-dark:#9aab07;
  --ink:#1d1d1d;
  --muted:#6d6d6d;
  --name-blue:#2c63b8;
  --black:#0b0b0b;
}
*{margin:0;padding:0;box-sizing:border-box}
html,body{width:1200px;height:3822px;overflow:hidden;background:#fff}
body{position:relative;font-family:'Roboto',sans-serif;color:var(--ink)}
.abs{position:absolute}
.head{font-family:'Kumbh Sans',sans-serif;font-weight:800}
.center{text-align:center}
/* header */
.topbar{top:0;left:0;width:1200px;height:64px;background:#fff}
.contact-item{display:flex;align-items:center;gap:12px;font-size:16px;font-weight:500;top:15px}
.ic-circle{width:34px;height:34px;border-radius:50%;background:var(--green);display:flex;align-items:center;justify-content:center}
.navbar{top:64px;left:0;width:1200px;height:44px;background:var(--blue)}
.nav-link{color:#fff;font-size:13px;font-weight:500;top:78px}
.logo-tab{top:44px;left:505px;width:190px;height:64px}
.wordmark{font-family:'Kumbh Sans',sans-serif;font-weight:800;color:var(--blue);letter-spacing:.5px}
.btn{border-radius:30px;color:#fff;font-weight:700;display:flex;align-items:center;justify-content:center;gap:8px}
.btn-green{background:var(--green)}
.btn-blue{background:var(--blue)}
/* hero */
.hero-media{top:108px;left:0;width:1200px;height:720px;background:radial-gradient(ellipse at 50% 55%,#5fd0ff 0%,#1568a8 25%,#0d2f5c 55%,#061428 85%)}
.hero-title{top:215px;left:0;width:1200px;color:#fff;font-size:56px;line-height:56px;text-shadow:0 3px 10px rgba(0,0,0,.5)}
.hero-text{top:338px;left:230px;width:740px;color:#fff;font-size:14px;line-height:26px;font-weight:500;text-shadow:0 1px 4px rgba(0,0,0,.7)}
/* stats */
.stat{width:220px;top:858px}
.stat .ic{width:58px;height:58px;border-radius:50%;background:#e8eef3;margin:0 auto 14px;display:flex;align-items:center;justify-content:center}
.stat .label{font-size:15px;font-weight:500}
.stat .num{font-size:21px;font-weight:700;margin-top:6px}
.section-title{font-size:32px;left:0;width:1200px;text-align:center}
/* testimonials */
.card{width:311px;height:360px;top:1120px;background:#fff;border-radius:30px;box-shadow:0 6px 26px rgba(0,0,0,.1);padding:46px 20px 0}
.quote{font-family:'Kumbh Sans',sans-serif;font-size:96px;line-height:72px;color:var(--name-blue);font-weight:800;height:36px;overflow:visible}
.stars{color:var(--green);font-size:15px;letter-spacing:2px;margin:6px 0 12px}
.card h3{font-size:18px;font-weight:500;margin-bottom:18px}
.card p{font-size:14.5px;line-height:25px;color:var(--muted)}
.person{position:absolute;left:20px;top:262px;display:flex;align-items:center;gap:12px}
.avatar{width:48px;height:48px;border-radius:50%;background:linear-gradient(#d9c3ae,#8f7561)}
.person b{display:block;color:var(--name-blue);font-size:13px;font-weight:700}
.person span{font-size:13px;color:#444}
/* steps */
.step-img{top:1767px;width:311px;height:228px;border-radius:14px}
.step-label{top:2008px;width:311px;color:#fff;font-family:'Kumbh Sans',sans-serif;font-weight:800;font-size:21px;text-align:center}
/* team */
.member{width:180px;top:2484px;text-align:center}
.member .ph{width:90px;height:90px;border-radius:50%;margin:0 auto 12px;border:3px solid #e4e4e4;background:linear-gradient(#eaa78a,#7aa0c4)}
.member b{display:block;font-size:18px;font-weight:500}
.member span{font-size:15px;color:var(--muted);display:block;margin-top:8px}
/* pricing */
.plan{top:2820px;width:285px;height:370px;background:#fff;box-shadow:0 4px 22px rgba(0,0,0,.09);padding:38px 30px 0}
.plan h3{font-family:'Kumbh Sans',sans-serif;font-weight:600;font-size:25px}
.price{margin:12px 0 14px;display:flex;align-items:baseline;gap:8px}
.price strong{font-family:'Kumbh Sans',sans-serif;font-weight:800;color:var(--green);font-size:38px}
.price span{font-size:15px;font-weight:500}
.plan ul{list-style:none}
.plan li{font-size:14.5px;line-height:25px;margin-bottom:6px;padding-left:26px;position:relative}
.plan li em{font-style:normal;color:var(--blue);display:block}
.plan li::before{content:"";position:absolute;left:0;top:6px;width:13px;height:13px;border-radius:50%;background:var(--blue)}
.plan li::after{content:"";position:absolute;left:4px;top:9px;width:3px;height:5px;border:solid #fff;border-width:0 2px 2px 0;transform:rotate(45deg)}
.plan .btn{width:150px;height:40px;font-size:15px;margin-top:18px}
/* footer */
.footer{top:3370px;left:0;width:1200px;height:452px;background:var(--black);color:#fff}
.f-title{font-size:18px;font-weight:700;top:3476px}
.f-rule{top:3510px;width:62px;height:2px;background:#fff}
.f-links{top:3540px;font-size:11.5px;line-height:33px}
.f-contact{font-size:11.5px;line-height:20px;display:flex;gap:18px}
.social{top:3643px;width:28px;height:28px;border-radius:50%;background:#fff;color:#000;font-size:12px;font-weight:700;display:flex;align-items:center;justify-content:center}
.copy{top:3765px;left:0;width:1200px;height:57px;background:#000;font-size:13px;color:#fff}
</style>
</head>
<body>

<!-- header -->
<div class="abs topbar"></div>
<div class="abs contact-item" style="left:112px"><div class="ic-circle"><svg width="16" height="16" viewBox="0 0 24 24"><path fill="#fff" d="M6.6 10.8a15 15 0 0 0 6.6 6.6l2.2-2.2c.3-.3.7-.4 1-.2 1.1.4 2.3.6 3.6.6.6 0 1 .4 1 1V20c0 .6-.4 1-1 1A17 17 0 0 1 3 4c0-.6.4-1 1-1h3.5c.6 0 1 .4 1 1 0 1.3.2 2.5.6 3.6.1.3 0 .7-.2 1z"/></svg></div>+353 1 555 0148</div>
<div class="abs contact-item" style="left:322px;font-size:15px"><div class="ic-circle"><svg width="16" height="12" viewBox="0 0 16 12"><rect x="0.5" y="0.5" width="15" height="11" fill="none" stroke="#fff"/><path d="M1 1l7 6 7-6" fill="none" stroke="#fff"/></svg></div>info@tallomex-sample.com</div>
<div class="abs" style="left:826px;top:17px;width:34px;height:34px;border-radius:50%;background:#ddd;display:flex;align-items:center;justify-content:center"><svg width="14" height="14" viewBox="0 0 14 14"><circle cx="6" cy="6" r="4.5" fill="none" stroke="#222" stroke-width="2"/><path d="M9.5 9.5l3.5 3.5" stroke="#222" stroke-width="2"/></svg></div>
<div class="abs btn btn-green" style="left:872px;top:12px;width:215px;height:38px;font-size:15px;font-weight:500">Book an Appointment
<svg width="14" height="14" viewBox="0 0 14 14"><rect x="1" y="2.5" width="12" height="10.5" fill="none" stroke="#fff"/><path d="M1 5.5h12M4 1v3M10 1v3" stroke="#fff"/></svg></div>
<div class="abs navbar"></div>
<svg class="abs logo-tab" viewBox="0 0 190 64"><polygon points="0,0 190,0 160,64 30,64" fill="#fff"/></svg>
<div class="abs wordmark" style="top:38px;left:520px;width:160px;text-align:center;font-size:30px">Tallomex</div>
<div class="abs nav-link" style="left:128px">5 steps</div>
<div class="abs nav-link" style="left:197px">|</div>
<div class="abs nav-link" style="left:224px">Our Pricing</div>
<div class="abs nav-link" style="left:317px">|</div>
<div class="abs nav-link" style="left:345px">Ahead of the Curve</div>
<div class="abs nav-link" style="left:735px">Our Team</div>
<div class="abs nav-link" style="left:818px">|</div>
<div class="abs nav-link" style="left:845px">Contact Us</div>
<div class="abs nav-link" style="left:977px;font-weight:700">LOGIN &#9679;</div>
<svg class="abs" style="left:1062px;top:76px" width="22" height="20" viewBox="0 0 22 20"><path d="M1 2h3l2 10h11l2-7H6" fill="none" stroke="#fff" stroke-width="2"/><circle cx="8" cy="16" r="1.6" fill="#fff"/><circle cx="16" cy="16" r="1.6" fill="#fff"/><circle cx="18" cy="3" r="4" fill="var(--green)"/></svg>

<!-- hero -->
<div class="abs hero-media" role="img" aria-label="Photo: person walking down a glowing blue digital tunnel"></div>
<svg class="abs" style="left:0;top:680px" width="1200" height="150" viewBox="0 0 1200 150">
<path d="M0 40 C250 -10 550 80 800 105 C960 120 1080 90 1200 20 L1200 150 L0 150Z" fill="var(--green)"/>
<path d="M0 45 C250 30 520 70 760 95 C940 110 1080 100 1200 60 L1200 150 L0 150Z" fill="#fff"/>
</svg>
<h1 class="abs head hero-title center">Step into your Digital<br>Transformation</h1>
<p class="abs hero-text center">Digital transformation is a journey. At Tallomex we divide the journey into five key steps that take your business from comprehensive market research to full appointment bookings. Ready to go on that journey?</p>
<div class="abs btn btn-blue" style="left:516px;top:418px;width:167px;height:47px;font-size:14px;box-shadow:0 4px 14px rgba(0,0,0,.4)">START HERE &#10148;</div>

<!-- stats -->
<div class="abs stat center" style="left:139px"><div class="ic"><svg width="28" height="28" viewBox="0 0 28 28"><rect x="3" y="5" width="22" height="20" rx="2" fill="var(--blue)"/><rect x="3" y="5" width="22" height="5" fill="var(--blue-dark)"/><g fill="#fff"><rect x="7" y="13" width="3" height="3"/><rect x="12.5" y="13" width="3" height="3"/><rect x="18" y="13" width="3" height="3"/><rect x="7" y="18" width="3" height="3"/><rect x="12.5" y="18" width="3" height="3"/></g></svg></div><div class="label">Appointments Booked</div><div class="num">762</div></div>
<div class="abs stat center" style="left:381px"><div class="ic"><svg width="28" height="28" viewBox="0 0 28 28"><path d="M4 11h5l10-6v18L9 17H4z" fill="var(--blue)"/><path d="M22 9l4-2M22 14h4M22 19l4 2" stroke="var(--blue)" stroke-width="2"/></svg></div><div class="label">Marketing Campaigns</div><div class="num">31</div></div>
<div class="abs stat center" style="left:626px"><div class="ic"><svg width="28" height="28" viewBox="0 0 28 28"><rect x="3" y="5" width="22" height="18" rx="2" fill="var(--blue)"/><g fill="#fff"><rect x="8" y="14" width="3" height="6"/><rect x="13" y="11" width="3" height="9"/><rect x="18" y="13" width="3" height="7"/></g></svg></div><div class="label">Website Traffic Increase</div><div class="num">25%</div></div>
<div class="abs stat center" style="left:869px"><div class="ic"><svg width="28" height="28" viewBox="0 0 28 28"><path d="M14 3a8 8 0 0 0-5 14v4h10v-4A8 8 0 0 0 14 3z" fill="var(--blue)"/><rect x="10" y="22" width="8" height="3" fill="var(--blue-dark)"/></svg></div><div class="label">Creative Ideas</div><div class="num" style="font-size:24px;line-height:22px">&#8734;</div></div>

<!-- why us -->
<h2 class="abs head section-title" style="top:1045px">WHY OTHERS CHOOSE US?</h2>
<div class="abs card" style="left:111px"><div class="quote">&ldquo;</div><div class="stars">★★★★★</div><h3>100 bookings in first month!</h3><p>Tallomex's booking system helped us get over 100 appointment bookings in May 2020.</p><div class="person"><div class="avatar" role="img" aria-label="Client portrait"></div><div><b>LENA HARWICK</b><span>Owner, Shearline Studio</span></div></div></div>
<div class="abs card" style="left:445px"><div class="quote">&ldquo;</div><div class="stars">★★★★★</div><h3>From 55 new patients per month!</h3><p>Since Tallomex optimised our marketing campaigns we've had 55-75 new patients per month.</p><div class="person"><div class="avatar" role="img" aria-label="Client portrait"></div><div><b>DR. RAVI OKONJO</b><span>Owner, Brightbite Dental</span></div></div></div>
<div class="abs card" style="left:777px"><div class="quote">&ldquo;</div><div class="stars">★★★★★</div><h3>25% increase in web traffic!</h3><p>Tallomex have increased our Rankwise ranking by 20,000 and our web traffic by 25%</p><div class="person"><div class="avatar" role="img" aria-label="Client portrait"></div><div><b>TOMAS VERHOEVEN</b><span>CEO, LedgerPulse</span></div></div></div>

<!-- 5 steps band -->
<svg class="abs" style="left:0;top:1530px" width="1200" height="750" viewBox="0 0 1200 750">
<path d="M0 0 C120 70 280 110 440 110 C700 110 900 20 1200 30 L1200 550 C1000 560 800 580 600 640 C400 700 200 740 0 690Z" fill="var(--green)"/>
<path d="M0 80 C150 110 300 120 440 112 C700 90 900 30 1200 30 L1200 605 C1050 640 900 650 700 650 C450 650 250 760 0 690Z" fill="var(--blue)"/>
</svg>
<h2 class="abs head section-title" style="top:1698px;color:#fff;font-size:30px">5 STEPS</h2>
<div class="abs step-img" style="left:112px;background:linear-gradient(135deg,#c9b39c,#e9e4dc 60%,#d97d59)" role="img" aria-label="Photo: team planning creative campaign with colour swatches"></div>
<div class="abs step-img" style="left:445px;background:linear-gradient(135deg,#7ea6d8,#d9e3ef 55%,#b488c2)" role="img" aria-label="Photo: magnifying glass over printed market research charts"></div>
<div class="abs step-img" style="left:777px;background:linear-gradient(135deg,#8b6f57,#d9cfc3 50%,#3a3f4a)" role="img" aria-label="Photo: laptop showing an online booking page"></div>
<div class="abs step-label" style="left:112px">Creative Campaigns</div>
<div class="abs step-label" style="left:445px">Market Research</div>
<div class="abs step-label" style="left:777px">Online Bookings</div>
<svg class="abs" style="left:56px;top:1876px" width="14" height="20" viewBox="0 0 14 20"><path d="M11 2L3 10l8 8" fill="none" stroke="#fff" stroke-width="2.5"/></svg>
<svg class="abs" style="left:1128px;top:1876px" width="14" height="20" viewBox="0 0 14 20"><path d="M3 2l8 8-8 8" fill="none" stroke="#fff" stroke-width="2.5"/></svg>
<div class="abs btn btn-green" style="left:517px;top:2077px;width:166px;height:47px;font-size:14px">SIGN UP &#10148;</div>

<!-- team -->
<h2 class="abs head section-title" style="top:2343px">OUR TEAM</h2>
<p class="abs center" style="top:2394px;left:210px;width:780px;font-size:15px;line-height:26px;color:var(--muted)">rom business management and web development to creative campaign delivery and social media expertise, our team has all the experience your business needs to it to the top of its digital game.</p>
<div class="abs member" style="left:74px"><div class="ph" role="img" aria-label="Team member portrait"></div><b>Declan</b><span>Account Manager</span></div>
<div class="abs member" style="left:247px"><div class="ph" role="img" aria-label="Team member portrait"></div><b>Oisin</b><span>Account Manager</span></div>
<div class="abs member" style="left:419px"><div class="ph" role="img" aria-label="Team member portrait"></div><b>Niamh</b><span>Website Specia</span></div>
<div class="abs member" style="left:591px"><div class="ph" role="img" aria-label="Team member portrait"></div><b>Kavya</b><span>Web developer</span></div>
<div class="abs member" style="left:765px"><div class="ph" role="img" aria-label="Team member portrait"></div><b>Marian</b><span>Content Creator</span></div>
<div class="abs member" style="left:935px"><div class="ph" role="img" aria-label="Team member portrait"></div><b>Rosalind</b><span>Social media speciali</span></div>

<!-- pricing -->
<h2 class="abs head section-title" style="top:2708px">OUR PRICING</h2>
<p class="abs center" style="top:2758px;left:0;width:1200px;font-size:15px;color:var(--muted)">Which plan you take will depend on how many steps you want to take on your digital transformation journey.</p>
<div class="abs plan" style="left:134px"><h3>Starter Plan</h3><div class="price"><strong>€399</strong><span>/a month</span></div><ul><li><em>Step 1:</em>Online readiness review based on our 12 point checklist</li><li><em>Step 2:</em>Implementation</li></ul><div class="btn btn-green">Take 2 steps</div></div>
<div class="abs plan" style="left:458px"><h3>Premium Plan</h3><div class="price"><strong>€599</strong><span>/a month</span></div><ul><li><em>Step 1:</em>Steps 1, 2 &amp; 3</li><li><em>Step 3:</em>Content is King</li></ul><div class="btn btn-green">Take 3 steps</div></div>
<div class="abs plan" style="left:781px"><h3>Ultimate Plan</h3><div class="price"><strong>€899</strong><span>/a month</span></div><ul><li><em>Step 1:</em>Steps 1, 2, 3, 4 &amp; 5</li><li><em>Step 4:</em>Marketing Campaign</li><li><em>Step 5:</em>Monitor and Maintain</li></ul><div class="btn btn-green" style="width:166px">Take the full journey</div></div>

<!-- footer -->
<svg class="abs" style="left:0;top:3270px" width="1200" height="110" viewBox="0 0 1200 110">
<path d="M0 90 C150 40 300 0 520 10 C760 20 900 110 1200 60 L1200 110 L0 110Z" fill="var(--green)"/>
<path d="M0 110 C200 60 350 30 540 40 C760 50 920 120 1200 90 L1200 110Z" fill="var(--black)"/>
</svg>
<div class="abs footer"></div>
<div class="abs wordmark" style="top:3505px;left:110px;font-size:44px">Tallomex</div>
<div class="abs f-title" style="left:386px;color:#fff">QUICK LINKS</div><div class="abs f-rule" style="left:386px"></div>
<div class="abs f-links" style="left:391px;color:#fff">5 steps<br>Our Pricing<br>Ahead of the Curve<br>Our Team<br>Contact Us</div>
<div class="abs f-title" style="left:580px;color:#fff">CONTACT US</div><div class="abs f-rule" style="left:580px"></div>
<div class="abs f-contact" style="left:584px;top:3540px;color:#fff"><span>&#9990;</span>+353 1 555 0148</div>
<div class="abs f-contact" style="left:584px;top:3582px;color:#fff"><span>&#9993;</span>info@tallomex-sample.com</div>
<div class="abs f-contact" style="left:584px;top:3616px;color:#fff;width:200px"><span>&#9679;</span><div>Unit 4 Harbour Enterprise Park, Quay Road, Kilbrenna, Co. Westmeath Ireland N91 X7QK</div></div>
<div class="abs f-title" style="left:832px;color:#fff">SUBSCRIBE TO OUR BLOG</div><div class="abs f-rule" style="left:832px"></div>
<p class="abs" style="left:837px;top:3538px;width:240px;font-size:11.5px;line-height:20px;color:#fff">Sign up today to get resources on how to attract and retain more customers!</p>
<div class="abs" style="left:838px;top:3590px;width:252px;height:34px;border-radius:18px;background:#fff;font-size:10px;color:#888;padding:11px 14px">&#9993; Email Address</div>
<div class="abs" style="left:1042px;top:3590px;width:48px;height:34px;border-radius:0 18px 18px 0;background:var(--name-blue);display:flex;align-items:center;justify-content:center"><svg width="16" height="14" viewBox="0 0 16 14"><path d="M1 6l14-5-4 12-3-5z" fill="#fff"/></svg></div>
<div class="abs social" style="left:834px">f</div>
<div class="abs social" style="left:871px">&#9675;</div>
<div class="abs social" style="left:908px">in</div>
<div class="abs copy"></div>
<div class="abs" style="top:3785px;left:110px;font-size:13px;color:#fff">Copyright© 2024 Tallomex | All Rights Reserved</div>
<div class="abs" style="top:3785px;left:844px;font-size:13px;color:#fff">Terms and Conditions &nbsp; | &nbsp; Privacy Policy</div>
<div class="abs" style="top:3787px;left:1131px;font-size:11px;color:#fff">C47</div>

</body>
</html>
```